SkyvornQ Business Cards and Stationary Design

Need a design for our business cards and stationary. I want to carry on the theme of the logo. I want the business cards to have a design on the back. I would like the business cards and the stationary to carry the same theme, design scheme, and branding

Target Market(s)

Airlines and Maintenance Facilities

Industry/Entity Type

Aviation

Contact Information for Business Card

Name
Position Title
Address: 4827 Trellis Hollow Road, Fort Pierce, Florida, 34951
Office Number
Mobile Number
Email
Website

Font styles to use
Serif
Sans Serif

Colors

Designer to choose colors to be used in the design.

```html
<!DOCTYPE html>
<html lang="en">
<head>
<meta charset="utf-8">
<title>SkyvornQ Business Card</title>
<link rel="stylesheet" href="https://fonts.googleapis.com/css2?family=Roboto:wght@400;500;700;900&display=swap">
<style>
  :root {
    --backdrop: #dcdcdc;
    --card-white: #f2f2f2;
    --navy: #0d2f6b;
    --navy-deep: #0a2a5e;
    --sky: #0a9ee0;
    --sky-bright: #1ab0ee;
    --ink: #3c3c3c;
    --brand-ink: #13315f;
    --white: #ffffff;
  }
  html, body {
    margin: 0;
    padding: 0;
    width: 1200px;
    height: 960px;
    overflow: hidden;
    background: var(--backdrop);
    font-family: "Roboto", Arial, sans-serif;
  }
  .card {
    position: absolute;
    width: 600px;
    height: 342px;
    overflow: hidden;
    box-shadow: 0 2px 4px rgba(0,0,0,0.35);
  }
  .card-front { left: 314px; top: 113px; background: var(--card-white); }
  .card-back {
    left: 311px; top: 472px; height: 343px;
    background: radial-gradient(ellipse 330px 260px at 290px 195px, var(--sky-bright) 0%, #0a7cc8 45%, var(--navy-deep) 100%);
  }
  .swoop { position: absolute; left: 0; top: 0; }
  .holder {
    position: absolute; right: 20px; top: 33px;
    text-align: right; color: var(--white);
  }
  .holder-name { font-size: 21px; font-weight: 700; letter-spacing: 0.3px; line-height: 1; }
  .holder-title { font-size: 14px; font-weight: 500; margin-top: 4px; line-height: 1; }
  .brand {
    position: absolute; left: 34px; top: 92px;
    display: flex; flex-direction: column; align-items: center;
  }
  .brand-dot {
    width: 70px; height: 70px; border-radius: 50%;
    border: 6px solid var(--sky); box-sizing: border-box; margin-bottom: 12px;
  }
  .brand-name {
    font-size: 27px; font-weight: 900; letter-spacing: 4px; color: var(--brand-ink); line-height: 1;
  }
  .contacts {
    position: absolute; left: 34px; top: 257px;
    list-style: none; margin: 0; padding: 0;
    font-size: 14px; color: var(--ink);
  }
  .contacts li { display: flex; align-items: center; height: 18.5px; }
  .contacts svg { width: 13px; height: 13px; margin-right: 9px; fill: var(--navy); }
  .address {
    position: absolute; right: 39px; top: 258px;
    font-size: 14px; color: var(--ink); text-align: right; line-height: 18.5px; font-style: normal;
  }
  .back-brand {
    position: absolute; left: 32px; top: 279px; color: var(--white);
  }
  .back-name { font-size: 25px; font-weight: 900; letter-spacing: 4.5px; line-height: 1; }
  .back-web { font-size: 13px; letter-spacing: 3.6px; margin-top: 3px; line-height: 1; }
</style>
</head>
<body>
  <section class="card card-front">
    <svg class="swoop" width="600" height="342" viewBox="0 0 600 342" aria-hidden="true">
      <defs>
        <radialGradient id="bandGlow" cx="300" cy="20" r="320" gradientUnits="userSpaceOnUse">
          <stop offset="0" stop-color="#0aa2e4"/>
          <stop offset="0.6" stop-color="#0a6cbc"/>
          <stop offset="1" stop-color="#0b3577"/>
        </radialGradient>
      </defs>
      <path d="M0,0 H600 V184 Q420,20 160,38 Q60,45 0,60 Z" fill="url(#bandGlow)"/>
      <path d="M0,60 Q60,45 160,38 Q420,20 600,184" fill="none" stroke="#0a2a5e" stroke-width="5"/>
      <path d="M0,57 Q60,42 160,35 Q420,17 600,181" fill="none" stroke="#cfe3f5" stroke-width="1"/>
    </svg>
    <div class="holder">
      <div class="holder-name">MARCUS DELANEY</div>
      <div class="holder-title">CEO/FOUNDER</div>
    </div>
    <div class="brand">
      <div class="brand-dot"></div>
      <div class="brand-name">SKYVORNQ</div>
    </div>
    <ul class="contacts">
      <li><svg viewBox="0 0 24 24" aria-hidden="true"><path d="M6.6 10.8a15.2 15.2 0 0 0 6.6 6.6l2.2-2.2c.3-.3.7-.4 1-.2 1.1.4 2.3.6 3.6.6.6 0 1 .4 1 1V20c0 .6-.4 1-1 1A17 17 0 0 1 3 4c0-.6.4-1 1-1h3.5c.6 0 1 .4 1 1 0 1.3.2 2.5.6 3.6.1.3 0 .7-.2 1z"/></svg>772 514 0396</li>
      <li><svg viewBox="0 0 24 24" aria-hidden="true"><path d="M7 1h10a2 2 0 0 1 2 2v18a2 2 0 0 1-2 2H7a2 2 0 0 1-2-2V3a2 2 0 0 1 2-2zm0 3v14h10V4zm5 15.5a1.2 1.2 0 1 0 0 2.4 1.2 1.2 0 0 0 0-2.4z"/></svg>772 829 4170</li>
      <li><svg viewBox="0 0 24 24" aria-hidden="true"><path d="M2 5h20v14H2zm2 2v.5l8 5 8-5V7zm0 3v7h16v-7l-8 5z"/></svg>info@skyvornq.com</li>
    </ul>
    <address class="address">
      4827 Trellis Hollow Road<br>
      Fort Pierce, Florida, 34951<br>
      www.skyvornq.com
    </address>
  </section>

  <section class="card card-back">
    <div class="back-brand">
      <div class="back-name">SKYVORNQ</div>
      <div class="back-web">www.skyvornq.com</div>
    </div>
  </section>
</body>
</html>
```